Fenwick Grading LTD - website for irrigation & Landscape Lighting & Buried service wire

Looking for a website to help promote my business with Irrigation (installation, service, etc) and buried service wire/drainage solutions.

Commercial/Residential

Landscape lighting.

I’ll get photos in the trucks and trailers to upload as well maybe the machine as well.

Target Market(s)

Homeowners who want green grass and beautiful gardens. Beautiful landscape lighting

Industry/Entity Type

Irrigation systems and landscape lighting and buried service wire to homes and offering Drainage soltions.

Coding

Coded - Design and coding required

Number of Pages Required

4 page

Colors
F0912C
F2A743
F7CA91
FBE8D2
FDF5EE

Requirements
Must have
• was hoping to link up my email on fenwickgrading@mailbox-example.net with the website if possible.
Nice to have
• Page for Irrigation, page for landscape lighting, page buried service wire & drainage soltions.

```html
<!DOCTYPE html>
<html lang="en">
<head>
<meta charset="UTF-8">
<title>Fenwick Grading LTD</title>
<link href="https://fonts.googleapis.com/css2?family=Montserrat:wght@400;500;600;700&display=swap" rel="stylesheet">
<style>
:root{
  --orange:#F0912C;
  --orange-2:#F2A743;
  --orange-3:#F7CA91;
  --cream:#FBE8D2;
  --cream-light:#FDF5EE;
  --ink:#1d1d1d;
  --text:#555;
  --slate:#6e6e6e;
  --black:#000;
  --white:#fff;
}
*{margin:0;padding:0;box-sizing:border-box}
html,body{width:1200px;height:4199px;overflow:hidden;background:var(--white)}
body{font-family:'Montserrat',sans-serif;color:var(--ink)}
.page{position:relative;width:1200px;height:4199px;overflow:hidden}
.abs{position:absolute}

/* header */
.site-header{position:absolute;left:0;top:0;width:1200px;height:85px;background:var(--cream-light);z-index:3}
.brand-box{position:absolute;left:98px;top:0;width:198px;height:124px;background:var(--white);border-radius:0 0 14px 14px;box-shadow:0 3px 10px rgba(0,0,0,.2);display:flex;flex-direction:column;align-items:center;justify-content:center;gap:8px}
.brand-box .mark{width:26px;height:26px;background:var(--orange);border-radius:50%}
.brand-box .name{font-weight:700;font-size:18px;color:var(--orange);text-align:center;line-height:1.15;text-transform:uppercase}
.main-nav{position:absolute;left:375px;top:36px;display:flex;gap:17px;font-size:12px;font-weight:600;text-transform:uppercase}
.btn-solid{position:absolute;background:var(--orange);color:var(--white);font-weight:600;font-size:15px;display:flex;align-items:center;justify-content:center}
.btn-outline{position:absolute;border:2px solid var(--white);color:var(--white);font-weight:600;font-size:15px;display:flex;align-items:center;justify-content:center}

/* hero */
.hero{position:absolute;left:0;top:85px;width:1200px;height:592px;background:linear-gradient(120deg,#4f7d2a 0%,#6fa038 35%,#8c8c82 60%,#b5b3aa 80%,#6c8a43 100%)}
.hero-title{position:absolute;left:106px;top:148px;font-size:31px;font-weight:600;line-height:38px;color:var(--white);text-transform:uppercase;white-space:nowrap}

/* headings */
.section-title{position:absolute;left:0;width:1200px;text-align:center;font-size:38px;font-weight:600;text-transform:uppercase}
.underline{position:absolute;left:555px;width:90px;height:4px;background:var(--orange)}

/* services */
.service-card{position:absolute;top:848px;width:312px;height:409px;border-radius:8px;box-shadow:0 4px 12px rgba(0,0,0,.2);overflow:hidden}
.service-card .label{position:absolute;left:0;bottom:32px;width:100%;text-align:center;color:var(--white);font-size:21px;font-weight:600}
.arrow{position:absolute;width:48px;height:48px;border:2px solid var(--orange);border-radius:50%;background:var(--white);display:flex;align-items:center;justify-content:center}

/* about */
.about{position:absolute;left:0;top:1337px;width:1200px;height:575px;background:var(--slate)}
.about-mark{position:absolute;left:100px;top:150px;width:480px;display:flex;align-items:center;justify-content:center;gap:16px}
.about-mark .dot{width:40px;height:40px;border-radius:50%;background:var(--orange-2)}
.about-mark .name{font-size:40px;font-weight:600;color:var(--orange-3);text-transform:uppercase}
.about-title{position:absolute;left:600px;top:100px;font-size:38px;font-weight:600;color:var(--white)}
.about-line{position:absolute;left:600px;top:163px;width:85px;height:4px;background:var(--white)}
.about-text{position:absolute;left:601px;top:188px;width:430px;font-size:13px;line-height:26px;color:var(--white)}

/* gallery */
.gallery-tile{position:absolute;width:322px;height:331px;border-radius:6px}

/* cta */
.cta{position:absolute;left:0;top:2885px;width:1200px;height:360px;background:linear-gradient(180deg,#d98426,#e9912f 60%,#c98030)}
.cta-title{position:absolute;left:0;top:82px;width:1200px;text-align:center;color:var(--white);font-size:25px;font-weight:600;line-height:36px;text-transform:uppercase}

/* testimonials */
.review{position:absolute;top:3400px;width:315px;height:360px;background:var(--white);box-shadow:0 2px 10px rgba(0,0,0,.15)}
.review .avatar{position:absolute;left:103px;top:22px;width:108px;height:108px;border-radius:50%;background:linear-gradient(160deg,#cfd4d8,#8a99a6)}
.review .who{position:absolute;top:145px;width:100%;text-align:center;font-size:16px;font-weight:500}
.review .role{position:absolute;top:170px;width:100%;text-align:center;font-size:13px;color:var(--orange-2)}
.review .quote-mark{position:absolute;left:12px;top:178px;font-size:34px;font-weight:700;color:var(--ink);line-height:1}
.review .words{position:absolute;left:22px;top:210px;width:272px;text-align:center;font-size:13px;line-height:26px;color:var(--text)}
.review .stars{position:absolute;left:0;top:315px;width:100%;text-align:center;color:#f5b400;font-size:18px;letter-spacing:1px}

/* footer */
.site-footer{position:absolute;left:0;top:3814px;width:1200px;height:385px;background:var(--black);color:var(--white)}
.foot-brand{position:absolute;left:106px;top:100px;width:200px;display:flex;align-items:center;gap:10px}
.foot-brand .mark{width:22px;height:22px;border:2px solid var(--white);flex:none}
.foot-brand .name{font-size:22px;font-weight:600;line-height:1.15;text-transform:uppercase}
.social{position:absolute;top:256px;width:32px;height:32px;border:2px solid var(--white);border-radius:50%}
.foot-col{position:absolute;top:104px}
.foot-col h3{font-size:24px;font-weight:600;margin-bottom:16px}
.foot-col li{list-style:none;font-size:13.5px;height:30px;line-height:30px;display:flex;align-items:center;gap:8px}
.foot-rule{position:absolute;left:108px;top:329px;width:976px;height:1px;background:#888}
.copyright{position:absolute;left:0;top:349px;width:1200px;text-align:center;font-size:13px}
</style>
</head>
<body>
<div class="page">

  <header class="site-header">
    <div class="brand-box">
      <span class="mark"></span>
      <span class="name">Fenwick Grading<br>LTD</span>
    </div>
    <nav class="main-nav">
      <span>Home</span><span>About us</span><span>Irrigation</span><span>Service</span><span>Landscape lighting</span><span>Fiber optic</span>
    </nav>
    <a class="btn-solid" style="left:950px;top:20px;width:134px;height:45px">Contact Us</a>
  </header>

  <section class="hero" role="img" aria-label="Green lawn with a curving paved brick pathway through landscaped gardens">
    <h1 class="hero-title">Homeowners who<br>want green grass and<br>beautiful gardens.<br>Beautiful landscape<br>lighting</h1>
    <a class="btn-outline" style="left:108px;top:360px;width:137px;height:46px">Get Started</a>
  </section>
  <svg class="abs" style="left:0;top:600px" width="1200" height="90" viewBox="0 0 1200 90">
    <path d="M0 14 Q300 30 600 77 Q900 30 1200 14 L1200 90 L0 90Z" fill="var(--orange)"/>
    <path d="M0 26 Q300 44 600 90 Q900 44 1200 26 L1200 90 L0 90Z" fill="var(--white)"/>
  </svg>

  <h2 class="section-title" style="top:744px">Our Services</h2>
  <div class="underline" style="top:806px"></div>

  <div class="arrow" style="left:28px;top:1039px"><svg width="18" height="18" viewBox="0 0 18 18"><path d="M11 3 L5 9 L11 15" fill="none" stroke="var(--orange)" stroke-width="2"/></svg></div>
  <div class="arrow" style="left:1125px;top:1039px"><svg width="18" height="18" viewBox="0 0 18 18"><path d="M7 3 L13 9 L7 15" fill="none" stroke="var(--orange)" stroke-width="2"/></svg></div>

  <article class="service-card" style="left:99px;background:linear-gradient(180deg,#7ea84a,#4d7a2c 60%,#3a3f36)" role="img" aria-label="Lawn sprinkler watering flowers in a garden">
    <span class="label">Irrigation Installs</span>
  </article>
  <article class="service-card" style="left:438px;background:linear-gradient(180deg,#7fa44c,#64913a 45%,#6b6a66 75%,#3e3e3c)" role="img" aria-label="Paved path curving across a green lawn">
    <span class="label">Landscape Lighting</span>
  </article>
  <article class="service-card" style="left:779px;background:linear-gradient(160deg,#9a8a6a,#3b4a5e 50%,#222a33)" role="img" aria-label="Technician testing fiber optic cables with a handheld meter">
    <span class="label">Fiber Optic installation</span>
  </article>

  <section class="about">
    <div class="about-mark"><span class="dot"></span><span class="name">Fenwick Grading</span></div>
    <h2 class="about-title">ABOUT US</h2>
    <div class="about-line"></div>
    <p class="about-text">Lorem Ipsum is simply dummy text of the printing and typesetting industry. Lorem Ipsum has been the industry's standard dummy text ever since the 1500s, when an unknown printer took a galley of type and scrambled it to make a type specimen book. It has survived not only five centuries, but also the leap into electronic typesetting, remaining essentially unchanged. It was popularised in the 1960s with the release of Letraset sheets containing Lorem Ipsum passages, and more recently with desktop publishing software like Aldus</p>
    <a class="btn-solid" style="left:601px;top:441px;width:136px;height:44px">Read More</a>
  </section>
  <svg class="abs" style="left:0;top:1337px" width="1200" height="40" viewBox="0 0 1200 40">
    <path d="M0 0 L1200 0 L1200 4 Q900 14 600 34 Q300 14 0 4Z" fill="var(--white)"/>
    <path d="M0 4 Q300 14 600 34 Q900 14 1200 4 L1200 10 Q900 20 600 30 Q300 20 0 10Z" fill="var(--orange)"/>
  </svg>

  <h2 class="section-title" style="top:1996px">Our Gallery</h2>
  <div class="underline" style="left:547px;top:2060px;width:85px"></div>

  <div class="gallery-tile" style="left:91px;top:2098px;background:linear-gradient(180deg,#8fb1d6,#3e4a5f 55%,#6b7a4c)" role="img" aria-label="Blue craftsman house with stone porch"></div>
  <div class="gallery-tile" style="left:437px;top:2098px;background:linear-gradient(180deg,#9aa4a0,#4a5450 45%,#6aa03c)" role="img" aria-label="Dark green house with walkway across lawn"></div>
  <div class="gallery-tile" style="left:782px;top:2098px;background:linear-gradient(180deg,#2e2a26,#5a4636 50%,#a06a3a)" role="img" aria-label="Lit garden path with flowers at dusk"></div>
  <div class="gallery-tile" style="left:91px;top:2445px;background:linear-gradient(180deg,#5e7b9c,#2c2a2a 45%,#7d7f82)" role="img" aria-label="Modern house with lit garage and paved driveway"></div>
  <div class="gallery-tile" style="left:437px;top:2445px;background:linear-gradient(180deg,#9fbcc4,#7d9a7e 35%,#b59a78 60%,#4f8a2e)" role="img" aria-label="Stone retaining wall with evergreen shrubs"></div>
  <div class="gallery-tile" style="left:782px;top:2445px;background:linear-gradient(180deg,#a8c4de,#4e6a99 40%,#9c8c74 70%,#6b8a3c)" role="img" aria-label="Two storey house with garage and front lawn"></div>

  <section class="cta" role="img" aria-label="Sprinkler watering a lawn under orange tint">
    <h2 class="cta-title">Irrigation systems and landscape lighting and fiber<br>optic installation to homes</h2>
    <div class="abs" style="left:560px;top:167px;width:80px;height:4px;background:var(--white)"></div>
    <a class="btn-outline" style="left:533px;top:204px;width:135px;height:44px">Contact Us</a>
  </section>
  <svg class="abs" style="left:0;top:3205px" width="1200" height="45" viewBox="0 0 1200 45">
    <path d="M0 40 Q600 0 1200 40 L1200 45 L0 45Z" fill="#8a8a8a"/>
    <path d="M0 45 Q600 14 1200 45Z" fill="var(--white)"/>
  </svg>

  <h2 class="section-title" style="top:3300px">What our clients say</h2>
  <div class="underline" style="top:3362px"></div>

  <div class="arrow" style="left:28px;top:3568px"><svg width="18" height="18" viewBox="0 0 18 18"><path d="M11 3 L5 9 L11 15" fill="none" stroke="var(--orange)" stroke-width="2"/></svg></div>
  <div class="arrow" style="left:1125px;top:3568px"><svg width="18" height="18" viewBox="0 0 18 18"><path d="M7 3 L13 9 L7 15" fill="none" stroke="var(--orange)" stroke-width="2"/></svg></div>

  <article class="review" style="left:108px">
    <div class="avatar" role="img" aria-label="Client portrait"></div>
    <div class="who">Anderson</div><div class="role">Client</div>
    <div class="quote-mark">“</div>
    <p class="words">Lorem Ipsum is simply dummy text of the printing and typesetting industry. Lorem Ipsum has been the industry's standard dummy text ever since the</p>
    <div class="stars">★★★★★</div>
  </article>
  <article class="review" style="left:440px">
    <div class="avatar" role="img" aria-label="Client portrait"></div>
    <div class="who">Robin</div><div class="role">Client</div>
    <div class="quote-mark">“</div>
    <p class="words">Lorem Ipsum is simply dummy text of the printing and typesetting industry. Lorem Ipsum has been the industry's standard dummy text ever since the</p>
    <div class="stars">★★★★★</div>
  </article>
  <article class="review" style="left:771px">
    <div class="avatar" role="img" aria-label="Client portrait"></div>
    <div class="who">jessica</div><div class="role">Client</div>
    <div class="quote-mark">“</div>
    <p class="words">Lorem Ipsum is simply dummy text of the printing and typesetting industry. Lorem Ipsum has been the industry's standard dummy text ever since the</p>
    <div class="stars">★★★★★</div>
  </article>

  <footer class="site-footer">
    <svg class="abs" style="left:0;top:0" width="1200" height="50" viewBox="0 0 1200 50">
      <path d="M0 0 L1200 0 Q900 14 600 44 Q300 14 0 0Z" fill="var(--orange)"/>
      <path d="M0 0 L1200 0 Q900 6 600 30 Q300 6 0 0Z" fill="var(--white)"/>
    </svg>
    <div class="foot-brand"><span class="mark"></span><span class="name">Fenwick Grading LTD</span></div>
    <span class="social" style="left:109px"></span>
    <span class="social" style="left:163px"></span>
    <span class="social" style="left:214px"></span>

    <div class="foot-col" style="left:396px"><h3>Quick links</h3>
      <ul><li>Home</li><li>About us</li><li>Services</li><li>Testimonials</li><li>Contact Us</li></ul></div>
    <div class="foot-col" style="left:619px"><h3>Service Links</h3>
      <ul><li>Irrigation Service</li><li>Landscape Lighting</li><li>Fiber Optic installation</li></ul></div>
    <div class="foot-col" style="left:859px"><h3>Contact Info</h3>
      <ul>
        <li><svg width="14" height="10" viewBox="0 0 14 10"><rect x="0.5" y="0.5" width="13" height="9" fill="var(--white)"/><path d="M0.5 0.5 L7 6 L13.5 0.5" fill="none" stroke="var(--black)"/></svg>fenwickgrading@mailbox-example.net</li>
        <li><svg width="14" height="14" viewBox="0 0 14 14"><path d="M3 1 L5.5 4 L4 6 Q6 9 8 10 L10 8.5 L13 11 L11 13 Q3 12 1 3Z" fill="var(--white)"/></svg>+1 555 010 0188</li>
        <li><svg width="14" height="16" viewBox="0 0 14 16"><path d="M7 1 A5 5 0 0 1 12 6 Q12 9 7 15 Q2 9 2 6 A5 5 0 0 1 7 1Z" fill="none" stroke="var(--white)" stroke-width="2"/><circle cx="7" cy="6" r="1.8" fill="var(--white)"/></svg>100,ipsum lorem Ipsum</li>
        <li style="padding-left:22px">Is Simply Lorem ipsum</li>
      </ul></div>

    <div class="foot-rule"></div>
    <p class="copyright">Copyright © 2024 Fenwick Grading LTD | All Rights Reserved</p>
  </footer>
</div>
</body>
</html>
```